New Website for World Wide Charity (KOLVAN)

We need a dynamic web design for our brand new charity organisation that will be working worldwide. We will be funded by donations so need to attract people to donate.

What We Do
We work to optimise the wellbeing of the planet, the animals and all that live within. Our slogan is Achieving Vibrational Equilibrium.

We have included a Powerpoint document which may help you understand what we need, it is just an idea for structure and style, it is not set in stone so feel free to be as creative as you like!
Updates

Designs look the same

Target Market(s)

Adults 18+ with an interest in animal, environmental. Businesses that may like to support our natural world or already support our natural world.

Number of Pages Required

3 page

Colors

Designer to choose colors to be used in the design.

Requirements
Must have
• We need the website to be easy to use and understand.

Web pages will be Home, What We Do, Who We Are, Success Stories, What You Can Do (Blog section), Seek Help, Donate, Join.
Nice to have
• Natural feel, easy to navigate, Ideally the website will look natural and organic.

Natural colours, blues, greens, sand, gold, brown, grey, silver, Orange and yellow for impact.
Should not have
• Should not have a dark coloured theme.

```html
<!DOCTYPE html>
<html lang="en">
<head>
<meta charset="utf-8">
<title>KOLVAN – Achieving Vibrational Equilibrium</title>
<link rel="stylesheet" href="https://fonts.googleapis.com/css2?family=Arimo:wght@400&family=Roboto:wght@400;500&display=swap">
<style>
:root{
  --navy:#25337a;
  --navy-dark:#1c2866;
  --nav-active:#3d6fb4;
  --lavender:#c9a8d8;
  --teal:#128c74;
  --accent:#138a6f;
  --ink:#2b2b2b;
  --body:#555555;
  --white:#ffffff;
}
*{margin:0;padding:0;box-sizing:border-box}
html,body{width:1200px;height:2997px;overflow:hidden;background:var(--white);font-family:'Roboto',sans-serif;color:var(--ink)}
.page{position:relative;width:1200px;height:2997px}
a{text-decoration:none}

/* header */
.site-header{position:absolute;left:0;top:0;width:1200px;height:149px;background:var(--white);z-index:3}
.brand{position:absolute;left:110px;top:20px;width:216px;height:216px;border-radius:50%;background:var(--white);display:flex;align-items:center;justify-content:center;z-index:4}
.brand-name{font-size:26px;font-weight:400;color:var(--navy);letter-spacing:1px}
.cta{position:absolute;top:27px;height:46px;border-radius:23px;color:var(--white);font-size:16px;display:flex;align-items:center;justify-content:center}
.cta-donate{left:838px;width:121px;background:linear-gradient(90deg,#dcb4e2,#bf92d2)}
.cta-join{left:966px;width:122px;background:linear-gradient(90deg,#2b3d8c,var(--navy-dark))}
.main-nav{position:absolute;top:104px;left:0;font-size:13.5px;font-weight:500;color:var(--ink)}
.main-nav span{position:absolute;white-space:nowrap}
.main-nav .active{color:var(--nav-active)}

/* hero */
.hero-art{position:absolute;left:0;top:149px}
.hero-copy{position:absolute;left:111px;top:358px}
.hero-title{font-size:31px;font-weight:500;color:var(--navy)}
.hero-sub{margin-top:16px;font-size:20px;font-weight:500;color:#2f3a3a}
.hero-btn{position:absolute;left:112px;top:463px;width:193px;height:54px;border-radius:27px;background:var(--navy);color:var(--white);font-size:15px;font-weight:500;display:flex;align-items:center;justify-content:center}

/* cause cards */
.cause-card{position:absolute;top:986px;width:309px;height:403px;border-radius:7px;overflow:hidden}
.cause-card .art{position:absolute;inset:0}
.cause-card .shade{position:absolute;left:0;right:0;bottom:0;height:170px;background:linear-gradient(180deg,rgba(0,0,0,0),rgba(0,0,0,.75))}
.cause-title{position:absolute;left:0;right:0;top:300px;text-align:center;color:var(--white);font-size:19px;font-weight:500}
.cause-btn{position:absolute;left:90px;top:332px;width:129px;height:40px;border:1.5px solid var(--white);border-radius:20px;color:var(--white);font-size:12px;font-weight:500;display:flex;align-items:center;justify-content:center}

/* feature rows */
.feature-art{position:absolute;width:600px;height:313px}
.feature-text{position:absolute;width:405px}
.feature-text h2{font-size:24px;font-weight:500;color:#333333}
.feature-text .rule{width:46px;height:3px;background:var(--accent);margin:14px 0 28px}
.feature-text p{font-family:'Arimo',Arial,sans-serif;font-size:14.2px;line-height:25.7px;color:var(--body);text-align:justify}

/* footer */
.site-footer{position:absolute;left:0;top:2490px}
.footer-col{position:absolute;top:2625px;color:var(--white)}
.footer-col h3{font-size:23px;font-weight:400;margin-bottom:22px}
.footer-col li{list-style:none;font-size:15.5px;height:32.6px}
.footer-col li::before{content:"»";margin-right:16px;font-size:14px}
.footer-brand{position:absolute;left:117px;top:2851px;width:136px;height:136px;border-radius:50%;background:var(--white);display:flex;align-items:center;justify-content:center}
.footer-brand .brand-name{font-size:18px}
.footer-nav{position:absolute;top:2880px;left:0;color:var(--white);font-size:13.5px;font-weight:500}
.footer-nav span{position:absolute;white-space:nowrap}
.footer-meta{position:absolute;top:2942px;color:var(--white);font-size:13.5px;font-weight:500;white-space:nowrap}
</style>
</head>
<body>
<div class="page">

  <header class="site-header">
    <a class="cta cta-donate">DONATE</a>
    <a class="cta cta-join">JOIN</a>
    <nav class="main-nav">
      <span class="active" style="left:509px">HOME</span>
      <span style="left:582px">WHAT WE DO</span>
      <span style="left:699px">WHO WE ARE</span>
      <span style="left:816px">SUCCESS STORIES</span>
      <span style="left:968px">WHAT YOU CAN DO</span>
    </nav>
  </header>
  <div class="brand"><span class="brand-name">KOLVAN</span></div>

  <svg class="hero-art" width="1200" height="736" viewBox="0 0 1200 736" role="img" aria-label="Children and a bear silhouetted with forest textures, running through a sunny meadow with birds in flight">
    <defs>
      <linearGradient id="heroSky" x1="0" y1="0" x2="0" y2="1">
        <stop offset="0" stop-color="#c6e6e0"/>
        <stop offset=".4" stop-color="#dbe9c6"/>
        <stop offset=".68" stop-color="#b3cf78"/>
        <stop offset=".85" stop-color="#6f9f42"/>
        <stop offset="1" stop-color="#3a6e2a"/>
      </linearGradient>
      <radialGradient id="heroSun" cx=".58" cy=".62" r=".35">
        <stop offset="0" stop-color="#f6f2b8" stop-opacity=".9"/>
        <stop offset="1" stop-color="#f6f2b8" stop-opacity="0"/>
      </radialGradient>
      <radialGradient id="heroLeft" cx=".25" cy=".72" r=".25">
        <stop offset="0" stop-color="#3f7d45" stop-opacity=".75"/>
        <stop offset="1" stop-color="#3f7d45" stop-opacity="0"/>
      </radialGradient>
      <radialGradient id="heroRight" cx=".68" cy=".45" r=".3">
        <stop offset="0" stop-color="#4f9048" stop-opacity=".6"/>
        <stop offset="1" stop-color="#4f9048" stop-opacity="0"/>
      </radialGradient>
      <clipPath id="heroClip"><path d="M0 0H1200V613Q600 859 0 613Z"/></clipPath>
    </defs>
    <g clip-path="url(#heroClip)">
      <rect width="1200" height="736" fill="url(#heroSky)"/>
      <rect width="1200" height="736" fill="url(#heroSun)"/>
      <rect width="1200" height="736" fill="url(#heroRight)"/>
      <rect width="1200" height="736" fill="url(#heroLeft)"/>
    </g>
  </svg>

  <div class="hero-copy">
    <h1 class="hero-title">HELP RAISE WORLD VIBRATION</h1>
    <p class="hero-sub">ACHIEVING VIBRATIONAL EQUILIBRIUM</p>
  </div>
  <a class="hero-btn">MAKE A DIFFERENCE</a>

  <section>
    <div class="cause-card" style="left:112px">
      <div class="art" role="img" aria-label="Sunlit green forest foliage" style="background:radial-gradient(circle at 25% 10%,rgba(240,235,170,.85),rgba(240,235,170,0) 40%),radial-gradient(circle at 75% 35%,rgba(120,200,170,.7),rgba(120,200,170,0) 45%),linear-gradient(180deg,#8fbf6a,#3f9a5a 45%,#2a6a2a 75%,#1b3a1a)"></div>
      <div class="shade"></div>
      <div class="cause-title">ENVIRONMENT</div>
      <a class="cause-btn">FIND OUT MORE</a>
    </div>
    <div class="cause-card" style="left:446px">
      <div class="art" role="img" aria-label="Hummingbird feeding from a purple flower" style="background:radial-gradient(circle at 90% 8%,rgba(150,140,230,.9),rgba(150,140,230,0) 30%),radial-gradient(circle at 55% 50%,rgba(120,110,90,.7),rgba(120,110,90,0) 40%),linear-gradient(180deg,#5a3fb0,#6b55b8 40%,#6f7a5a 75%,#6a7a4a)"></div>
      <div class="shade" style="background:linear-gradient(180deg,rgba(0,0,0,0),rgba(40,50,20,.55))"></div>
      <div class="cause-title">ANIMAL</div>
      <a class="cause-btn">FIND OUT MORE</a>
    </div>
    <div class="cause-card" style="left:779px">
      <div class="art" role="img" aria-label="Family silhouettes holding hands at sunset" style="background:radial-gradient(ellipse at 60% 62%,rgba(240,170,90,.9),rgba(240,170,90,0) 35%),linear-gradient(180deg,#5f7fb0,#8f9db5 40%,#3a3a40 58%,#161616 80%)"></div>
      <div class="shade"></div>
      <div class="cause-title">HUMAN</div>
      <a class="cause-btn">FIND OUT MORE</a>
    </div>
  </section>

  <section>
    <div class="feature-art" style="left:0;top:1481px;background:radial-gradient(ellipse at 70% 15%,rgba(255,255,255,.8),rgba(255,255,255,0) 35%),radial-gradient(ellipse at 40% 65%,rgba(120,190,60,.8),rgba(120,190,60,0) 40%),linear-gradient(180deg,#aebfc4,#c9d4d0 30%,#4f8a3a 52%,#2f6a22 72%,#1e3f14)" role="img" aria-label="Wind turbines over green fields"></div>
    <div class="feature-text" style="left:653px;top:1530px">
      <h2>ENVIRONMENT</h2><div class="rule"></div>
      <p>Sed ut perspiciatis unde omnis iste natus error sit voluptatem accus antium doloremque laudantium, totam rem aperiam, eaque ipsa quae ab illo inventore veritatis et quasi architecto beatae vitae dicta sunt explicabo. Nemo enim ipsam voluptatem quia voluptas sit aspernatur aut odit aut fugit, sed quia consequuntur magni dolores eos qui ratione voluptatem sequi nesciunt.</p>
    </div>

    <div class="feature-text" style="left:141px;top:1843px">
      <h2>ANIMAL</h2><div class="rule"></div>
      <p>Sed ut perspiciatis unde omnis iste natus error sit voluptatem accus antium doloremque laudantium, totam rem aperiam, eaque ipsa quae ab illo inventore veritatis et quasi architecto beatae vitae dicta sunt explicabo. Nemo enim ipsam voluptatem quia voluptas sit aspernatur aut odit aut fugit, sed quia consequuntur magni dolores eos qui ratione voluptatem sequi nesciunt.</p>
    </div>
    <div class="feature-art" style="left:600px;top:1794px;background:radial-gradient(ellipse at 72% 52%,rgba(110,70,35,.75),rgba(110,70,35,0) 18%),radial-gradient(ellipse at 50% 80%,rgba(190,200,80,.7),rgba(190,200,80,0) 45%),linear-gradient(180deg,#26401c,#3f5a22 40%,#7f8f32 68%,#5a7a2a)" role="img" aria-label="Brown bear walking through a grassy forest clearing"></div>

    <div class="feature-art" style="left:0;top:2107px;background:radial-gradient(ellipse at 80% 70%,rgba(245,170,80,.95),rgba(245,170,80,0) 30%),linear-gradient(180deg,#5a7fb5,#9fadc2 40%,#2e3440 62%,#151515 85%)" role="img" aria-label="Long line of people holding hands, silhouetted at sunset"></div>
    <div class="feature-text" style="left:653px;top:2157px">
      <h2>HUMAN</h2><div class="rule"></div>
      <p>Sed ut perspiciatis unde omnis iste natus error sit voluptatem accus antium doloremque laudantium, totam rem aperiam, eaque ipsa quae ab illo inventore veritatis et quasi architecto beatae vitae dicta sunt explicabo. Nemo enim ipsam voluptatem quia voluptas sit aspernatur aut odit aut fugit, sed quia consequuntur magni dolores eos qui ratione voluptatem sequi nesciunt.</p>
    </div>
  </section>

  <footer>
    <svg class="site-footer" width="1200" height="507" viewBox="0 0 1200 507">
      <path d="M0 106Q600 -92 1200 106Z" fill="#c9a8d8"/>
      <path d="M0 110Q600 -78 1200 110V507H0Z" fill="#128c74"/>
    </svg>
    <div class="footer-col" style="left:206px">
      <h3>GET INVOLVED</h3>
      <ul><li>Join Us</li><li>Fundraise</li><li>Donate</li><li>Shop</li></ul>
    </div>
    <div class="footer-col" style="left:545px">
      <h3>GET HELP</h3>
      <ul><li>Contact Us</li><li>Media</li></ul>
    </div>
    <div class="footer-col" style="left:858px">
      <h3>LEGAL</h3>
      <ul><li>Terms and Conditions</li><li>Cookies</li><li>Privacy Policy</li></ul>
    </div>
    <div class="footer-brand"><span class="brand-name">KOLVAN</span></div>
    <nav class="footer-nav">
      <span style="left:421px">HOME</span>
      <span style="left:495px">WHAT WE DO</span>
      <span style="left:612px">WHO WE ARE</span>
      <span style="left:730px">SUCCESS STORIES</span>
      <span style="left:881px">WHAT YOU CAN DO</span>
      <span style="left:1036px">DONATE</span>
    </nav>
    <div class="footer-meta" style="left:420px">CHARITY NUMBE : 987654321</div>
    <div class="footer-meta" style="left:675px">© COPYRIGHTS 2021 KOLVAN. ALL RIGHTS RESERVED</div>
  </footer>

</div>
</body>
</html>
```